Simple, 1-Page Project - Life-saving AED Devices

We recently kicked off a project to bring all geographic location records for automatic emergency defibrillators (AEDs) in the State of New York online (instead of kept in paper in drawers). This hope is that is will ultimately save thousands of lives, as 9-1-1 operators will be able to quickly direct civilians to the nearest AED to bring to people suffering a cardiac event (e.g., a heart attack).

This page will be used to describe this effort, our progress thus far and how far we have left to go.

I am looking for a 1-page design - coded for both a responsive version for mobile devices and a traditional version - that would ***ideally*** plug into my existing WordPress site (https://qv-lmt.org), but it's not a requirement.

Target Market(s)

General public (non-physicians/non-EMTs)

Requirements
Must have
• - Our logo (please note, our logo is the Birchfield Vale Chapter logo...attached)
Nice to have
• - Would be wonderful to have an area with a clickable map showing where the participating regions are - which, once clicked, will take to you their specific sites. Regions are large chunks of land encompassing multiple towns, NOT a singular, specific place A nice-looking Google Map, a la Plumtail Grids (https://plumtailgrids.com/) would be cool if this were possible..
• - If you need a headline or page title, you can use: "Bringing AEDs in New York Online"
• - Would be nice if the design incorporated the color scheme of our brand (see attachment) and/or our main website: https://qv-lmt.org/
• - Would be nice to have some AED imagery - I attached some common symbols seen in AED advertising for inspiration
Should not have
• - This is a serious topic, so the design should be respectful and not too silly/cartoonish
• - Stock images, if chosen, should be thoughtful and classy

```html
<!DOCTYPE html>
<html lang="en">
<head>
<meta charset="utf-8">
<title>Bringing AEDs in New York Online</title>
<link href="https://fonts.googleapis.com/css2?family=Libre+Baskerville:ital,wght@0,400;0,700;1,400&family=EB+Garamond:ital,wght@0,400;0,600;1,400&display=swap" rel="stylesheet">
<style>
:root{
  --navy:#0d2f66;
  --navy-deep:#0a2757;
  --grey:#e5e5e6;
  --ink:#2b2b2b;
  --muted:#555a63;
  --white:#ffffff;
  --line:#d9d9d9;
}
*{box-sizing:border-box;margin:0;padding:0}
html,body{width:1200px;height:5038px;overflow:hidden}
body{position:relative;background:var(--white);font-family:"EB Garamond",Georgia,serif;color:var(--ink)}
.abs{position:absolute}
.serif-head{font-family:"Libre Baskerville",Georgia,serif;color:#1a1a1a;font-weight:700}

/* header */
.site-header{left:0;top:0;width:1200px;height:94px;background:var(--white)}
.brand{display:flex;align-items:center;gap:12px}
.brand-mark{width:58px;height:58px;border-radius:50%;background:var(--navy)}
.brand-name{font-family:"Libre Baskerville",Georgia,serif;color:var(--navy);font-size:15px;line-height:17px;letter-spacing:.5px;text-transform:uppercase}
.site-header .brand{position:absolute;left:110px;top:18px}
.main-nav{position:absolute;right:112px;top:36px;display:flex;gap:46px;font-size:15px;letter-spacing:.6px;text-transform:uppercase;color:#333}

/* hero */
.hero{left:0;top:94px;width:1200px;height:690px;background:linear-gradient(160deg,#c9a37a 0%,#8e7d66 30%,#5f7898 55%,#3f5878 80%,#4c4c4c 100%)}
.hero-title{left:0;top:288px;width:1200px;text-align:center;font-family:"Libre Baskerville",Georgia,serif;font-weight:700;font-size:58px;line-height:64px;color:var(--white);text-shadow:0 2px 6px rgba(0,0,0,.45)}
.btn-hero{left:533px;top:452px;width:134px;height:44px;border-radius:22px;background:var(--navy);border:2px solid var(--white);color:var(--white);font-size:14px;font-weight:600;letter-spacing:.4px;display:flex;align-items:center;justify-content:center;text-transform:uppercase}
.hero-dots{left:561px;top:736px;display:flex;gap:6px}
.hero-dots span{width:8px;height:8px;border-radius:50%;background:var(--white)}
.hero-curve{left:0;top:690px}

.grey-band{left:0;top:782px;width:1200px;height:1760px;background:var(--grey)}

/* welcome */
.welcome-title{left:0;top:840px;width:1200px;text-align:center;font-size:44px}
.welcome-text{left:270px;top:912px;width:660px;text-align:center;font-size:16px;line-height:26px;color:var(--muted)}

/* feature rows */
.feature-photo{border-radius:50%;width:586px;height:586px}
.feature-photo.crescent-right{box-shadow:12px 14px 0 var(--navy)}
.feature-photo.crescent-left{box-shadow:-12px 14px 0 var(--navy)}
.feature-copy{width:440px}
.feature-copy h2{font-size:29px;line-height:33px;font-weight:700;color:#1a1a1a;font-family:"Libre Baskerville",Georgia,serif}
.feature-copy .rule{width:62px;height:3px;background:var(--navy);margin:20px 0 22px}
.feature-copy p{font-size:16px;line-height:23px;color:var(--muted)}
.btn-outline{display:inline-flex;align-items:center;justify-content:center;margin-top:22px;width:122px;height:42px;border:2px solid var(--navy);border-radius:21px;color:var(--navy);font-weight:600;font-size:17px}

/* map */
.map-swoop{left:0;top:2440px}
.region-map{left:0;top:2533px;width:1200px;height:597px;background:linear-gradient(135deg,#eef0e6 0%,#f3eedb 45%,#b9d3ea 70%,#e9efe0 100%)}

/* reviews */
.reviews-title{left:0;top:3205px;width:1200px;text-align:center;font-size:44px}
.review-card{top:3305px;width:315px;height:220px;background:var(--white);border:1px solid var(--line);box-shadow:0 1px 4px rgba(0,0,0,.06);padding:20px 18px}
.review-avatar{position:absolute;left:18px;top:20px;width:76px;height:76px;border-radius:50%;background:linear-gradient(160deg,#c7a889,#6f7f96)}
.review-body{margin-left:92px}
.review-name{font-family:"Libre Baskerville",Georgia,serif;font-size:15px;font-weight:700;color:var(--navy);margin:8px 0 10px}
.review-quote{font-style:italic;font-size:14px;line-height:21px;color:var(--muted)}

/* AED section */
.aed-wave{left:0;top:3560px}
.aed-band{left:0;top:3736px;width:1200px;height:798px;background:var(--navy)}
.aed-rings{left:362px;top:3932px}
.aed-emblem{left:466px;top:4036px;width:272px;height:272px;border-radius:50%;background:radial-gradient(circle at 50% 62%,#f1c9cb 0%,#fbecec 45%,#ffffff 75%)}
.aed-lines{left:0;top:0;pointer-events:none}
.callout{width:230px;color:#c8d2e4}
.callout h3{font-family:"Libre Baskerville",Georgia,serif;font-size:15px;font-weight:700;color:var(--white);margin-bottom:8px}
.callout p{font-size:13.5px;line-height:19px}
.aed-icon{width:56px;height:56px;border-radius:50%;background:var(--white);border:3px solid #4a6797;display:flex;align-items:center;justify-content:center}

/* footer */
.site-footer{left:0;top:4534px;width:1200px;height:504px;background:var(--white)}
.site-footer .brand{position:absolute;left:110px;top:62px}
.social{position:absolute;left:954px;top:78px;display:flex;gap:8px}
.social span{width:28px;height:28px;border-radius:50%;background:var(--navy)}
.social span:last-child{background:#d8322f}
.footer-rule{position:absolute;left:110px;width:980px;height:1px;background:var(--line)}
.footer-col{position:absolute;top:175px;font-size:14px;line-height:22px;color:var(--muted)}
.footer-col h4{font-family:"EB Garamond",Georgia,serif;font-weight:400;font-size:17px;color:#333;margin-bottom:14px}
.contact-item{display:flex;gap:14px;margin-bottom:18px}
.contact-item svg{flex:none;margin-top:2px}
.copyright{position:absolute;left:0;top:462px;width:1200px;text-align:center;font-size:14px;color:#444}
</style>
</head>
<body>

<header class="abs site-header">
  <div class="brand"><span class="brand-mark"></span><span class="brand-name">Harbourline<br>Heart<br>Society</span></div>
  <nav class="main-nav"><span>Home</span><span>AED Devices</span><span>What We Do</span><span>About Us</span><span>News</span><span>Contact</span></nav>
</header>

<section>
  <div class="abs hero" role="img" aria-label="Photo of a bystander giving chest compressions to a person lying on a path"></div>
  <svg class="abs hero-curve" width="1200" height="100" viewBox="0 0 1200 100" aria-hidden="true">
    <path d="M0 52 Q600 130 1200 40 L1200 100 L0 100 Z" fill="#e5e5e6"/>
    <path d="M0 48 Q600 124 1200 36" fill="none" stroke="#0d2f66" stroke-width="6"/>
  </svg>
  <h1 class="abs hero-title">Bringing AEDs<br>in New York Online</h1>
  <a class="abs btn-hero">Read More</a>
  <div class="abs hero-dots"><span></span><span></span><span></span><span></span><span></span></div>
</section>

<div class="abs grey-band"></div>

<section>
  <h2 class="abs serif-head welcome-title">Welcome!</h2>
  <p class="abs welcome-text">Sed ut perspiciatis unde omnis iste natus error sit voluptatem accusantium doloremque laudantium, totam rem aperiam, eaque ipsa quae ab illo inventore veritatis Sed ut perspiciatis unde omnis iste natus error sit voluptatem accusantium doloremque laudantium</p>
</section>

<section>
  <div class="abs feature-photo crescent-right" style="left:-19px;top:1047px;background:linear-gradient(150deg,#dbd7d0,#9c9a97 50%,#5a4a48)" role="img" aria-label="Photo of a young man clutching his chest in pain"></div>
  <div class="abs feature-copy" style="left:655px;top:1193px">
    <h2>Sed ut perspiciatis undeom iste natuvoluptacusa.</h2><div class="rule"></div>
    <p>Sed ut perspiciatis unde omnis iste natus error sit voluptatem accusantium doloremque laudantium, totam rem aperiam, eaque ipsa quae ab illo inventore veritatis</p>
    <a class="btn-outline">Read More</a>
  </div>

  <div class="abs feature-photo crescent-left" style="left:626px;top:1458px;background:linear-gradient(140deg,#3a3a40,#b5232d 40%,#d9c9b0 70%,#c8b89f)" role="img" aria-label="Photo of a hand pressing the button on a red defibrillator"></div>
  <div class="abs feature-copy" style="left:110px;top:1731px">
    <h2>Sed ut perspiciatis undeom iste natuvoluptacusa.</h2><div class="rule"></div>
    <p>Sed ut perspiciatis unde omnis iste natus error sit voluptatem accusantium doloremque laudantium, totam rem aperiam, eaque ipsa quae ab illo inventore veritatis</p>
    <a class="btn-outline">Read More</a>
  </div>

  <div class="abs feature-photo crescent-right" style="left:-19px;top:2008px;background:linear-gradient(150deg,#e8e6e2,#a9b3c2 45%,#2f56a0 70%,#7a6a5e)" role="img" aria-label="Photo of responders using a defibrillator on a man lying down"></div>
  <div class="abs feature-copy" style="left:655px;top:2151px">
    <h2>Sed ut perspiciatis undeom iste natuvoluptacusa.</h2><div class="rule"></div>
    <p>Sed ut perspiciatis unde omnis iste natus error sit voluptatem accusantium doloremque laudantium, totam rem aperiam, eaque ipsa quae ab illo inventore veritatis</p>
    <a class="btn-outline">Read More</a>
  </div>
</section>

<section>
  <div class="abs region-map" role="img" aria-label="Map of New York State showing participating AED regions with pins"></div>
  <svg class="abs map-swoop" width="1200" height="100" viewBox="0 0 1200 100" aria-hidden="true">
    <path d="M0 100 Q700 90 1200 0 L1200 100 Z" fill="#0d2f66"/>
    <path d="M0 100 Q700 96 1200 42 L1200 100 Z" fill="#1c4a8c"/>
  </svg>
</section>

<section>
  <h2 class="abs serif-head reviews-title">Reviews</h2>
  <article class="abs review-card" style="left:111px">
    <div class="review-avatar" role="img" aria-label="Portrait of reviewer Halvard"></div>
    <div class="review-body"><h3 class="review-name">Halvard</h3>
    <p class="review-quote">"Lorem ipsum dolor sit amet conse ctetur adipiscing eli ed do iusmod tempm ipsum dolor sit amet, consectetur adiploorem ipsumdo lor, consecteturlore adipido"</p></div>
  </article>
  <article class="abs review-card" style="left:444px">
    <div class="review-avatar" role="img" aria-label="Portrait of reviewer Orlanne"></div>
    <div class="review-body"><h3 class="review-name">Orlanne</h3>
    <p class="review-quote">"Lorem ipsum dolor sit amet conse ctetur adipiscing eli ed do iusmod tempm ipsum dolor sit amet, consectetur adiploorem ipsumdo lor, consecteturlore adipido"</p></div>
  </article>
  <article class="abs review-card" style="left:774px">
    <div class="review-avatar" role="img" aria-label="Portrait of reviewer Tobin Wearsh"></div>
    <div class="review-body"><h3 class="review-name">Tobin Wearsh</h3>
    <p class="review-quote">"Lorem ipsum dolor sit amet conse ctetur adipiscing eli ed do iusmod tempm ipsum dolor sit amet, consectetur adiploorem ipsumdo lor, consecteturlore adipido"</p></div>
  </article>
</section>

<section>
  <svg class="abs aed-wave" width="1200" height="180" viewBox="0 0 1200 180" aria-hidden="true">
    <path d="M0 80 Q200 140 460 150 Q850 150 1200 0 L1200 180 L0 180 Z" fill="#0d2f66"/>
    <path d="M0 62 Q220 128 470 136 Q860 136 1200 -10" fill="none" stroke="#0d2f66" stroke-width="5"/>
    <path d="M850 130 Q1050 100 1200 40 L1200 60 Q1040 112 850 130 Z" fill="#ffffff"/>
  </svg>
  <div class="abs aed-band"></div>

  <svg class="abs aed-rings" width="480" height="480" viewBox="0 0 480 480" aria-hidden="true">
    <circle cx="240" cy="240" r="238" fill="#173c78" stroke="#6f86b0" stroke-width="1.5" stroke-dasharray="3 4"/>
    <circle cx="240" cy="240" r="196" fill="#1e4787"/>
    <circle cx="240" cy="240" r="172" fill="#2a5496"/>
    <circle cx="240" cy="240" r="154" fill="#4a6fab"/>
  </svg>
  <div class="abs aed-emblem" role="img" aria-label="AED emblem: the letters AED above a red heart with a lightning bolt"></div>

  <svg class="abs aed-lines" width="1200" height="5038" viewBox="0 0 1200 5038" aria-hidden="true">
    <g fill="none" stroke="#8ea2c6" stroke-width="1.5">
      <polyline points="706,3920 738,3878 806,3878"/>
      <polyline points="397,4012 380,3975 310,3975"/>
      <polyline points="836,4284 870,4284 884,4240 894,4240"/>
      <polyline points="433,4366 370,4366 350,4340 300,4340"/>
    </g>
  </svg>

  <div class="abs aed-icon" style="left:678px;top:3921px"><svg width="24" height="24" viewBox="0 0 24 24"><path d="M12 21 C5 16 2 12 3 8 C4 4 9 3 12 7 C15 3 20 4 21 8 C22 12 19 16 12 21 Z" fill="#0d2f66"/></svg></div>
  <div class="abs aed-icon" style="left:369px;top:4013px"><svg width="22" height="22" viewBox="0 0 24 24"><path d="M6 3 L9 3 L11 8 L8.5 10 C9.5 12.5 11.5 14.5 14 15.5 L16 13 L21 15 L21 18 C21 19.5 19.5 21 18 21 C10 20.5 3.5 14 3 6 C3 4.5 4.5 3 6 3 Z" fill="#0d2f66"/></svg></div>
  <div class="abs aed-icon" style="left:780px;top:4256px"><svg width="22" height="22" viewBox="0 0 24 24"><circle cx="12" cy="12" r="8" fill="none" stroke="#0d2f66" stroke-width="2.5"/><circle cx="12" cy="12" r="2.5" fill="#0d2f66"/></svg></div>
  <div class="abs aed-icon" style="left:435px;top:4338px"><svg width="24" height="24" viewBox="0 0 24 24"><circle cx="12" cy="7" r="4" fill="#0d2f66"/><path d="M3 21 C3 15 7 12 12 12 C17 12 21 15 21 21 Z" fill="#0d2f66"/></svg></div>

  <div class="abs callout" style="left:813px;top:3856px"><h3>Loresauae ailloventor</h3><p>Sed ut perspiciatis unde omnis iste natus error sit voluptatem accusantium dolore qror sit voluptatem accusantium.</p></div>
  <div class="abs callout" style="left:110px;top:3950px"><h3>Loresauae ailloventor</h3><p>Sed ut perspiciatis unde omnis iste natus error sit voluptatem accusantium dolore qror sit voluptatem accusantium.</p></div>
  <div class="abs callout" style="left:898px;top:4214px"><h3>Loresauae ailloventor</h3><p>Sed ut perspiciatis unde omnis iste natus error sit voluptatem accusantium dolore qror sit voluptatem accusantium.</p></div>
  <div class="abs callout" style="left:113px;top:4316px"><h3>Loresauae ailloventor</h3><p>Sed ut perspiciatis unde omnis iste natus error sit voluptatem accusantium dolore qror sit voluptatem accusantium.</p></div>
</section>

<footer class="abs site-footer">
  <div class="brand"><span class="brand-mark"></span><span class="brand-name">Harbourline<br>Heart<br>Society</span></div>
  <div class="social"><span></span><span></span><span></span><span></span></div>
  <div class="footer-rule" style="top:148px"></div>

  <div class="footer-col" style="left:110px">
    <h4>Contact</h4>
    <div class="contact-item"><svg width="20" height="24" viewBox="0 0 20 24"><path d="M10 23 C4 15 2 11 2 8 A8 8 0 0 1 18 8 C18 11 16 15 10 23 Z" fill="none" stroke="#0d2f66" stroke-width="1.6"/><circle cx="10" cy="8" r="3" fill="none" stroke="#0d2f66" stroke-width="1.6"/></svg><span>214 Larkmoor Lane,<br>Fenwick Row</span></div>
    <div class="contact-item"><svg width="22" height="22" viewBox="0 0 24 24"><path d="M6 3 L9 3 L11 8 L8.5 10 C9.5 12.5 11.5 14.5 14 15.5 L16 13 L21 15 L21 18 C21 19.5 19.5 21 18 21 C10 20.5 3.5 14 3 6 C3 4.5 4.5 3 6 3 Z" fill="none" stroke="#0d2f66" stroke-width="1.6"/></svg><span>8 800 555 014 22<br>8 800 555 097 31</span></div>
    <div class="contact-item"><svg width="24" height="20" viewBox="0 0 24 20"><rect x="1.5" y="2.5" width="21" height="15" fill="none" stroke="#0d2f66" stroke-width="1.6"/><polyline points="2,3 12,11 22,3" fill="none" stroke="#0d2f66" stroke-width="1.6"/></svg><span>info@example.com<br>lead@harbourline.example</span></div>
  </div>
  <div class="footer-col" style="left:415px">
    <h4>Company</h4>
    Lorem ipsum dolo<br>Fusce eget leo tincid<br>Donec consequat<br>Praesent elementum<br>Jmauris posueret<br>Aenean a ex eu lectu<br>Donec consequa
  </div>
  <div class="footer-col" style="left:675px">
    <h4>Advantages</h4>
    Lorem ipsum dolo<br>Fusce eget leo tincid<br>Donec consequat<br>Praesent elementum<br>Jmauris posueret<br>Donec consequa<br>Aenean a ex eu lectu
  </div>
  <div class="footer-col" style="left:925px">
    <h4>Other Links</h4>
    Lorem ipsum dolo<br>Consectetur adipiscing elit.<br>Fusce eget leo tincid<br>Praesent elementum<br>Jmauris posueret<br>Donec consequa<br>Aenean a ex eu lectu
  </div>

  <div class="footer-rule" style="top:434px"></div>
  <p class="copyright">Copyright 2019 All Rights Reserved</p>
</footer>

</body>
</html>
```